Brell Stone Company Business Cards

Front and Back Business Card - logo and text setup - cool design. I need workable photoshop or illustrator files so I can setup each employee card with design that is created
Updates

Hi everyone, thank you for the great entries. Please no more white and blue cards - there are so many already - black and silver only now please. thanks!

Target Market(s)

Construction Industry - Facility Managers

Industry/Entity Type

Construction

Contact Information for Business Card

I really like contemporary simplistic looks - clean neat....not opposed to seeing some black backrounds

Requirements
Must have
• Logo/website address with design on front only - www.brellstone-example.com (logo attached)
• Back:
• Name/Title/Company Address/Phone/email address
Nice to have
• Cool design
Should not have
• Nothing gimmicky like Fire or Water - since we are a Fire Protection company - it has all been done

```html
<!DOCTYPE html>
<html lang="en">
<head>
<meta charset="utf-8">
<title>Brell Stone Company Business Cards</title>
<link href="https://fonts.googleapis.com/css2?family=Open+Sans:wght@400;600;700;800&display=swap" rel="stylesheet">
<style>
  :root {
    --stage: #1c1c1e;
    --card-black: #050505;
    --brand-red: #ff2b2b;
    --brand-blue: #0a239c;
    --deep-blue: #06176e;
    --text-white: #ffffff;
    --text-soft: #e6e6e6;
  }
  * { margin: 0; padding: 0; box-sizing: border-box; }
  html, body {
    width: 1200px; height: 960px; overflow: hidden;
    background: var(--stage);
    font-family: "Open Sans", Arial, sans-serif;
  }
  .stage {
    position: relative; width: 1200px; height: 960px;
    display: flex; flex-direction: column; align-items: center; justify-content: center; gap: 40px;
  }
  .card {
    position: relative; width: 700px; height: 400px;
    background: var(--card-black); overflow: hidden;
    box-shadow: 0 10px 30px rgba(0,0,0,0.5);
  }
  .wordmark {
    color: var(--brand-red); font-weight: 800; letter-spacing: -1px; line-height: 1;
  }
  .card-front { display: flex; flex-direction: column; align-items: center; justify-content: center; }
  .card-front .wordmark { font-size: 84px; }
  .card-front .website {
    margin-top: 34px; color: var(--text-soft); font-size: 19px; letter-spacing: 5px;
  }
  .card-back .wordmark { position: absolute; left: 40px; top: 36px; font-size: 54px; }
  .person { position: absolute; left: 44px; top: 124px; color: var(--text-white); }
  .person-name { font-weight: 700; font-size: 19px; }
  .person-title { font-size: 16px; color: var(--text-soft); }
  .waves { position: absolute; inset: 0; }
  .contact-list {
    position: absolute; right: 32px; top: 284px; list-style: none;
    color: var(--text-white); font-size: 16px; text-align: right;
  }
  .contact-list li { display: flex; align-items: center; justify-content: flex-end; gap: 12px; height: 26px; }
  .contact-list svg { width: 16px; height: 16px; }
  .address {
    position: absolute; right: 60px; bottom: 12px; color: var(--text-white); font-size: 17px;
  }
</style>
</head>
<body>
<main class="stage">
  <section class="card card-front" aria-label="Card front">
    <div class="wordmark">Brell Stone</div>
    <div class="website">www.brellstone-example.com</div>
  </section>

  <section class="card card-back" aria-label="Card back">
    <svg class="waves" viewBox="0 0 700 400" aria-hidden="true">
      <path fill="var(--brand-red)" d="M0,176 C140,192 260,232 420,230 C560,228 640,244 700,256 L700,400 L0,400Z"/>
      <path fill="var(--card-black)" d="M0,190 C140,204 260,244 420,242 C560,240 640,256 700,267 L700,400 L0,400Z"/>
      <path fill="var(--brand-blue)" d="M0,200 C140,215 260,255 420,252 C560,250 640,265 700,276 L700,400 L0,400Z"/>
      <path fill="none" stroke="var(--deep-blue)" stroke-width="3" d="M0,218 C160,236 280,262 430,260 C560,258 640,270 700,282"/>
    </svg>
    <div class="wordmark">Brell Stone</div>
    <div class="person">
      <div class="person-name">Dana Mercer</div>
      <div class="person-title">President</div>
    </div>
    <ul class="contact-list">
      <li>(555) 014-2287
        <svg viewBox="0 0 16 16" aria-hidden="true"><path fill="#fff" d="M3 1h3l1 4-2 1c1 2 3 4 5 5l1-2 4 1v3c0 1-1 2-2 2C7 15 1 9 1 3c0-1 1-2 2-2z"/></svg>
      </li>
      <li>info@brellstone-example.com
        <svg viewBox="0 0 16 16" aria-hidden="true"><rect x="1" y="3" width="14" height="10" fill="#fff"/><path d="M1 3l7 6 7-6" fill="none" stroke="var(--brand-blue)" stroke-width="1.4"/></svg>
      </li>
      <li>www.brellstone-example.com
        <svg viewBox="0 0 16 16" aria-hidden="true"><g fill="none" stroke="#fff" stroke-width="1.3"><circle cx="8" cy="8" r="6.5"/><ellipse cx="8" cy="8" rx="3" ry="6.5"/><path d="M1.5 8h13M3 4.5h10M3 11.5h10"/></g></svg>
      </li>
    </ul>
    <div class="address">48 Harbor Point Road, Lindale, NY 10999</div>
  </section>
</main>
</body>
</html>
```